MRT Property - Business Cards

Looking for a business card & general letterhead, signage etc design for our new logo.

Colours:
000a20
0056a2
00b5ef
0088ce
68cef2

Fonts:
Poppins
Karla

Please keep look and feel of new brand - example in the zip package I sent.

```html
<!DOCTYPE html>
<html lang="en">
<head>
<meta charset="utf-8">
<title>MRT Property – Business Cards</title>
<link rel="stylesheet" href="https://fonts.googleapis.com/css2?family=Montserrat:wght@400;500&family=Poppins:wght@700&display=swap">
<style>
  :root{
    --ink:#000a20;
    --navy:#121628;
    --brand-blue:#0056a2;
    --mid-blue:#0088ce;
    --bright-blue:#00b5ef;
    --sky:#68cef2;
    --white:#ffffff;
    --backdrop:#1d1e23;
  }
  *{box-sizing:border-box;margin:0;padding:0}
  html,body{width:1200px;height:900px;overflow:hidden}
  body{background:var(--backdrop);position:relative;font-family:"Montserrat",sans-serif}

  .card{position:absolute;left:320px;width:560px;height:320px;border-radius:18px;overflow:hidden}

  /* Front */
  .card--front{top:60px;background:linear-gradient(135deg,#0a4fa0 0%,var(--brand-blue) 55%,#0b4a95 100%)}
  .card--front .pattern{position:absolute;inset:0;
    background:linear-gradient(200deg,rgba(0,20,70,.35) 0%,rgba(0,86,162,0) 50%,rgba(0,181,239,.45) 100%)}
  .card--front .wordmark{position:absolute;right:48px;top:120px;display:flex;align-items:center;gap:10px}
  .wordmark-dot{width:16px;height:16px;border-radius:50%;background:var(--sky)}
  .wordmark-name{font-family:"Poppins",sans-serif;font-weight:700;color:var(--white);font-size:26px;letter-spacing:.5px}

  /* Back */
  .card--back{top:420px;background:var(--navy)}
  .card--back .sail-mark{position:absolute;right:40px;top:20px;width:240px;height:240px;border-radius:50%;
    background:radial-gradient(circle at 55% 40%,#2a3462 0%,#161c3a 45%,rgba(18,22,40,0) 72%)}
  .card--back .edge-band{position:absolute;left:0;right:0;bottom:0;height:14px;background:var(--brand-blue)}
  .back-content{position:absolute;left:40px;top:40px;color:var(--white)}
  .back-wordmark{font-family:"Poppins",sans-serif;font-weight:700;font-size:46px;line-height:1;letter-spacing:.5px}
  .person{margin-top:26px}
  .person-name{font-size:22px;font-weight:500}
  .person-title{font-size:13px;margin-top:2px}
  .address{margin-top:16px;font-size:13px;line-height:1.35}
  .contacts{margin-top:14px;list-style:none;font-size:13px;line-height:1.55}
  .contacts li{display:flex;align-items:center;gap:10px}
  .contacts svg{width:13px;height:13px;fill:var(--mid-blue);flex:none}
</style>
</head>
<body>

<section class="card card--front" aria-label="Business card front">
  <div class="pattern" role="img" aria-label="Repeating brand sail pattern in blue tones"></div>
  <div class="wordmark">
    <span class="wordmark-dot"></span>
    <span class="wordmark-name">MRT Property</span>
  </div>
</section>

<section class="card card--back" aria-label="Business card back">
  <div class="sail-mark" role="img" aria-label="Large faint brand sail symbol"></div>
  <div class="back-content">
    <div class="back-wordmark">MRT Property</div>
    <div class="person">
      <div class="person-name">Daniel Reyes</div>
      <div class="person-title">Managing Director</div>
    </div>
    <div class="address">240 Harbor Line Road<br>Fairview, TN 37062</div>
    <ul class="contacts">
      <li><svg viewBox="0 0 24 24"><path d="M6.6 10.8a15.1 15.1 0 0 0 6.6 6.6l2.2-2.2a1 1 0 0 1 1-.25 11.4 11.4 0 0 0 3.6.57 1 1 0 0 1 1 1V20a1 1 0 0 1-1 1A17 17 0 0 1 3 4a1 1 0 0 1 1-1h3.5a1 1 0 0 1 1 1c0 1.25.2 2.45.57 3.57a1 1 0 0 1-.25 1z"/></svg>555.014.2290</li>
      <li><svg viewBox="0 0 24 24"><path d="M2 5h20v14H2z M2 5l10 8 10-8" /></svg>info@mrtproperty.com</li>
      <li><svg viewBox="0 0 24 24"><path d="M12 2a10 10 0 1 0 0 20 10 10 0 0 0 0-20zm6.9 6h-3a15.7 15.7 0 0 0-1.4-3.6A8 8 0 0 1 18.9 8zM12 4c.8 1.2 1.5 2.5 1.9 4h-3.8c.4-1.5 1.1-2.8 1.9-4zM4.3 14a8 8 0 0 1 0-4h3.4a16 16 0 0 0 0 4zm.8 2h3a15.7 15.7 0 0 0 1.4 3.6A8 8 0 0 1 5.1 16zm3-8h-3a8 8 0 0 1 4.4-3.6A15.7 15.7 0 0 0 8.1 8zM12 20c-.8-1.2-1.5-2.5-1.9-4h3.8c-.4 1.5-1.1 2.8-1.9 4zm2.3-6H9.7a14.6 14.6 0 0 1 0-4h4.6a14.6 14.6 0 0 1 0 4zm.2 5.6a15.7 15.7 0 0 0 1.4-3.6h3a8 8 0 0 1-4.4 3.6zm1.8-5.6a16 16 0 0 0 0-4h3.4a8 8 0 0 1 0 4z"/></svg>www.mrtproperty.com</li>
    </ul>
  </div>
  <div class="edge-band"></div>
</section>

</body>
</html>
```